Vodka Bottle Label - Luma Vodka

I need a bottle label for a vodka I'd like to make called Luma Vodka.
I would like a label that looks elegant and fresh. I would like some mountains and colours to be red and white. Open to other colours being added but not too colourful. "Luma" means fresh, dawn in polish, i would like if mountains or something extra was added to the label too. I would like the Luma Vodka name not to be too small.
The vodka is made in australia and is 37%.

I would love to have a little bit of gold colour in the label!

I will provide the back label words when completing my decision.

i'd like to make it more simple and less european looking. More australian.

I saw a bottle like this and i did like the concept.

https://www.tallgumcellars.com.au/spirits/qrnt-vodka-range?srsltid=ZtqWXkelmaHuP31-ra-m7s92xudhfew_pT8eWnGBbRTxLsb3hTyQsdGaqYt

Target Market(s)

Vodka Drinkers

Industry/Entity Type

Alcohol

Colors
EB3D1F
EC4F4E
F09395
F8D3D4
FCEDEE

Requirements
Must have
• red and white colours incorporated, mountains or freshness on it.
Nice to have
• Fresh and clean look. Classy

```html
<!DOCTYPE html>
<html lang="en">
<head>
<meta charset="utf-8">
<title>Luma Vodka – Bottle Label</title>
<link rel="stylesheet" href="https://fonts.googleapis.com/css2?family=Open+Sans:wght@400;600&display=swap">
<style>
  :root {
    --canvas-bg: #f4f1f1;
    --label-frost: #fdfafa;
    --label-edge: #f3e1e2;
    --red-strong: #eb3d1f;
    --red-soft: #ec4f4e;
    --rose: #f09395;
    --blush: #f8d3d4;
    --mist: #fcedee;
    --ink: #262a2c;
  }
  * { box-sizing: border-box; margin: 0; padding: 0; }
  html, body {
    width: 940px;
    height: 1200px;
    overflow: hidden;
    background: var(--canvas-bg);
    font-family: "Open Sans", Arial, sans-serif;
  }
  .canvas {
    position: relative;
    width: 940px;
    height: 1200px;
  }
  .label {
    position: absolute;
    left: 210px;
    top: 60px;
    width: 520px;
    height: 1080px;
    background: var(--label-frost);
    border: 1px solid var(--label-edge);
    border-radius: 6px;
    overflow: hidden;
    box-shadow: 0 18px 40px rgba(120, 60, 60, 0.10);
  }
  .brand-halo {
    position: absolute;
    left: 120px;
    top: 130px;
    width: 290px;
    height: 290px;
    border: 22px solid var(--mist);
    border-radius: 50%;
  }
  .brand-name {
    position: absolute;
    left: 205px;
    top: 120px;
    width: 130px;
    height: 420px;
    writing-mode: vertical-rl;
    transform: rotate(180deg);
    font-size: 128px;
    font-weight: 600;
    line-height: 130px;
    letter-spacing: 4px;
    color: var(--red-strong);
    text-align: center;
  }
  .product-type {
    position: absolute;
    left: 0;
    width: 100%;
    top: 575px;
    text-align: center;
    font-size: 30px;
    font-weight: 400;
    letter-spacing: 1px;
    color: var(--ink);
  }
  .mountain-art {
    position: absolute;
    left: 0;
    top: 650px;
    width: 100%;
    height: 310px;
    background: linear-gradient(180deg, rgba(252, 237, 238, 0) 0%, var(--mist) 22%, var(--blush) 55%, var(--rose) 100%);
  }
  .label-footer {
    position: absolute;
    left: 0;
    width: 100%;
    top: 985px;
    text-align: center;
    font-size: 21px;
    line-height: 1.3;
    color: var(--ink);
  }
</style>
</head>
<body>
  <main class="canvas">
    <section class="label">
      <div class="brand-halo" aria-hidden="true"></div>
      <h1 class="brand-name">LUMA</h1>
      <p class="product-type">VODKA</p>
      <div class="mountain-art" role="img" aria-label="Painted snowy mountain range at dawn across the lower label, in soft red and rose tones"></div>
      <p class="label-footer">Made In Australia<br>ALC. 37%VOL.</p>
    </section>
  </main>
</body>
</html>
```